Frostvale Harborline LLC

we need a business card design

Industry/Entity Type

hvac

Contact Information for Business Card

my logo

Requirements
Must have
• my logo and same colors

```html
<!DOCTYPE html>
<html lang="en">
<head>
<meta charset="utf-8">
<title>Frostvale Harborline LLC — Business Card</title>
<link rel="stylesheet" href="https://fonts.googleapis.com/css2?family=Montserrat:wght@400;500;700;800&display=swap">
<style>
  :root {
    --bg: #1c1c1e;
    --brand-blue: #1562ad;
    --brand-deep: #0f56a0;
    --brand-sky: #1ba9e1;
    --card-white: #ffffff;
    --ink: #3a3a3a;
  }
  * { box-sizing: border-box; margin: 0; padding: 0; }
  html, body { width: 1200px; height: 900px; overflow: hidden; }
  body {
    background: var(--bg);
    font-family: "Montserrat", sans-serif;
    position: relative;
  }
  .card {
    position: absolute;
    left: 250px;
    width: 700px;
    height: 400px;
    border-radius: 16px;
    overflow: hidden;
  }
  .card--front { top: 40px; background: var(--brand-blue); }
  .card--back { top: 480px; background: var(--card-white); }

  .brand-mark {
    display: flex;
    align-items: center;
    gap: 14px;
    font-weight: 800;
    letter-spacing: 0.5px;
  }
  .brand-mark__dot { width: 18px; height: 18px; border-radius: 50%; }

  .card--front .brand-mark {
    position: absolute;
    inset: 0;
    justify-content: center;
    color: var(--card-white);
    font-size: 34px;
  }
  .card--front .brand-mark__dot { background: var(--card-white); }

  .card--back .brand-mark {
    position: absolute;
    left: 48px;
    top: 56px;
    color: var(--brand-blue);
    font-size: 22px;
  }
  .card--back .brand-mark__dot { background: var(--brand-blue); }

  .holder {
    position: absolute;
    right: 40px;
    top: 44px;
    text-align: right;
  }
  .holder__name {
    font-size: 27px;
    font-weight: 800;
    color: var(--brand-deep);
    letter-spacing: 0.5px;
  }
  .holder__name span { color: var(--brand-sky); }
  .holder__role { font-size: 15px; color: var(--ink); margin-top: 2px; }
  .holder-tab {
    position: absolute;
    right: 0;
    top: 44px;
    width: 24px;
    height: 44px;
    background: var(--brand-deep);
  }

  .contact {
    position: absolute;
    left: 48px;
    top: 130px;
    color: var(--ink);
    font-size: 16px;
    line-height: 1.45;
  }
  .contact__address { margin-bottom: 12px; }
  .contact__list { list-style: none; }
  .contact__list li { display: flex; align-items: center; gap: 10px; }
  .contact__icon { width: 14px; height: 14px; flex: none; }

  .wave { position: absolute; left: 0; bottom: 0; width: 700px; height: 400px; }
</style>
</head>
<body>
  <section class="card card--front" aria-label="Card front">
    <div class="brand-mark"><span class="brand-mark__dot"></span>Frostvale Harborline LLC</div>
  </section>

  <section class="card card--back" aria-label="Card back">
    <svg class="wave" viewBox="0 0 700 400" aria-hidden="true">
      <path d="M0,338 C230,352 430,300 700,198 L700,214 C430,316 230,364 0,352 Z" fill="var(--brand-sky)"/>
      <path d="M0,352 C230,364 430,316 700,214 L700,400 L0,400 Z" fill="var(--brand-deep)"/>
    </svg>

    <div class="brand-mark"><span class="brand-mark__dot"></span>Frostvale Harborline LLC</div>

    <div class="holder-tab"></div>
    <div class="holder">
      <p class="holder__name">DORIAN <span>PELL</span></p>
      <p class="holder__role">Founder</p>
    </div>

    <div class="contact">
      <p class="contact__address">24 Quarry Ridge Ln<br>Westmere ABC 4410</p>
      <ul class="contact__list">
        <li>
          <svg class="contact__icon" viewBox="0 0 24 24" aria-hidden="true"><path fill="var(--brand-sky)" d="M6.6 10.8a15 15 0 0 0 6.6 6.6l2.2-2.2c.3-.3.7-.4 1-.2 1.1.4 2.3.6 3.6.6.6 0 1 .4 1 1V20c0 .6-.4 1-1 1A17 17 0 0 1 3 4c0-.6.4-1 1-1h3.5c.6 0 1 .4 1 1 0 1.3.2 2.5.6 3.6.1.3 0 .7-.2 1z"/></svg>
          303.555.0184
        </li>
        <li>
          <svg class="contact__icon" viewBox="0 0 24 24" aria-hidden="true"><path fill="var(--brand-sky)" d="M2 5h20v14H2z"/><path fill="none" stroke="#fff" stroke-width="2" d="M2 5l10 8 10-8"/></svg>
          hello@frostvaleharbor.com
        </li>
        <li>
          <svg class="contact__icon" viewBox="0 0 24 24" aria-hidden="true"><circle cx="12" cy="12" r="10" fill="var(--brand-sky)"/><path fill="none" stroke="#fff" stroke-width="1.4" d="M2 12h20M12 2c3 3 3 17 0 20M12 2c-3 3-3 17 0 20"/></svg>
          www.frostvaleharbor.com
        </li>
      </ul>
    </div>
  </section>
</body>
</html>
```